One Thumbnail for Online Shop for PowerPoint Templates needed

We are selling PowerPoint Templates and need therefore a thumbnail for our online shop.

You can use a stock photo, mock-ups or other design elements.

Format:
squared like 500 x 500
or wide like 1280 x 720

If you want to use a title, use:

"Graphs" ---> Title
"PowerPoint template" ---> subtitle

Attachments:
- OLD: Our old thumbnail which I do not like
- Template: PowerPoint pictures which you can use ( you can also copy them if you need more than these)
- Example: Some examples I found from other shops (please do not copy them exactly, only to show what I mean)

I received lots of designs until now but many are not what I have expected

Target Market(s)

E-Commerce

Industry/Entity Type

Shop

Font styles to use
Sans Serif

Requirements
Should not have
• Do NOT re-design one of the template.png (these are only examples, I will replace them later)

```html
<!DOCTYPE html>
<html lang="en">
<head>
<meta charset="utf-8">
<title>Standard Graphs – SlideCraft Presentation 1</title>
<link href="https://fonts.googleapis.com/css2?family=Raleway:wght@400;500&family=Arimo:wght@400;700&display=swap" rel="stylesheet">
<style>
  :root{
    --bg-deep:#1c2429;
    --bg-warm:#6b6258;
    --bg-light:#d9d6cf;
    --slide:#f7f8fa;
    --ink:#2b2b2b;
    --muted:#7d7d7d;
    --bar-light:#4a90d9;
    --bar-dark:#1f3d6b;
    --band:rgba(22,24,26,.82);
    --white:#ffffff;
  }
  *{margin:0;padding:0;box-sizing:border-box}
  html,body{width:1200px;height:750px;overflow:hidden;background:var(--bg-deep)}
  .canvas{position:relative;width:1200px;height:750px;overflow:hidden}
  .backdrop{position:absolute;inset:0;
    background:
      radial-gradient(ellipse 420px 300px at 180px 120px, rgba(240,238,232,.9), rgba(240,238,232,0) 70%),
      radial-gradient(ellipse 300px 260px at 720px 260px, rgba(220,226,232,.55), rgba(220,226,232,0) 70%),
      linear-gradient(180deg, var(--bg-light) 0%, var(--bg-warm) 45%, #3a3a36 65%, var(--bg-deep) 100%);}
  .slide{position:absolute;left:75px;width:312px;height:176px;background:var(--slide);
    box-shadow:0 2px 8px rgba(0,0,0,.25)}
  .slide svg{display:block;width:100%;height:100%}
  .slide--grid{top:80px}
  .slide--combo{top:295px}
  .slide--ranking{top:509px}
  .s-title{font:700 12.5px "Arimo",sans-serif;fill:var(--ink)}
  .s-sub{font:400 6.6px "Arimo",sans-serif;fill:var(--ink)}
  .s-head{font:700 5px "Arimo",sans-serif;fill:var(--ink)}
  .s-tiny{font:400 3.4px "Arimo",sans-serif;fill:var(--muted)}
  .s-label{font:400 4.6px "Arimo",sans-serif;fill:var(--muted)}
  .s-value{font:400 5.4px "Arimo",sans-serif;fill:var(--white)}
  .s-accent{font:400 5px "Arimo",sans-serif;fill:var(--bar-light)}
  .title-band{position:absolute;left:388px;top:556px;width:812px;height:128px;background:var(--band);
    text-align:right;padding-right:78px;color:var(--white);font-family:"Raleway",sans-serif}
  .title-band h1{font-weight:400;font-size:66px;line-height:1;padding-top:8px;letter-spacing:.5px}
  .title-band p{font-weight:400;font-size:37px;line-height:1;margin-top:6px;letter-spacing:1.5px}
</style>
</head>
<body>
<div class="canvas">
  <div class="backdrop" role="img" aria-label="Softly blurred photo of a desk by a bright window with a desktop monitor showing chart slides"></div>

  <!-- Slide: four small stacked bar charts -->
  <div class="slide slide--grid">
    <svg viewBox="0 0 385 217">
      <defs>
        <g id="bars-a">
          <rect x="0" y="-18" width="5" height="18" fill="var(--bar-light)"/><rect x="0" y="-10" width="5" height="10" fill="var(--bar-dark)"/>
          <rect x="9" y="-30" width="5" height="30" fill="var(--bar-light)"/><rect x="9" y="-18" width="5" height="18" fill="var(--bar-dark)"/>
          <rect x="18" y="-40" width="5" height="40" fill="var(--bar-light)"/><rect x="18" y="-20" width="5" height="20" fill="var(--bar-dark)"/>
          <rect x="27" y="-45" width="5" height="45" fill="var(--bar-light)"/><rect x="27" y="-22" width="5" height="22" fill="var(--bar-dark)"/>
          <rect x="36" y="-38" width="5" height="38" fill="var(--bar-light)"/><rect x="36" y="-20" width="5" height="20" fill="var(--bar-dark)"/>
          <rect x="45" y="-36" width="5" height="36" fill="var(--bar-light)"/><rect x="45" y="-20" width="5" height="20" fill="var(--bar-dark)"/>
          <rect x="54" y="-35" width="5" height="35" fill="var(--bar-light)"/><rect x="54" y="-18" width="5" height="18" fill="var(--bar-dark)"/>
          <rect x="63" y="-33" width="5" height="33" fill="var(--bar-light)"/><rect x="63" y="-18" width="5" height="18" fill="var(--bar-dark)"/>
          <rect x="72" y="-30" width="5" height="30" fill="var(--bar-light)"/><rect x="72" y="-17" width="5" height="17" fill="var(--bar-dark)"/>
          <rect x="81" y="-26" width="5" height="26" fill="var(--bar-light)"/><rect x="81" y="-15" width="5" height="15" fill="var(--bar-dark)"/>
          <rect x="90" y="-30" width="5" height="30" fill="var(--bar-light)"/><rect x="90" y="-16" width="5" height="16" fill="var(--bar-dark)"/>
          <rect x="99" y="-33" width="5" height="33" fill="var(--bar-light)"/><rect x="99" y="-18" width="5" height="18" fill="var(--bar-dark)"/>
          <line x1="-3" y1="0" x2="107" y2="0" stroke="#cfcfcf" stroke-width=".5"/>
        </g>
        <g id="bars-b">
          <rect x="0" y="-24" width="5" height="24" fill="var(--bar-light)"/><rect x="0" y="-16" width="5" height="16" fill="var(--bar-dark)"/>
          <rect x="9" y="-30" width="5" height="30" fill="var(--bar-light)"/><rect x="9" y="-16" width="5" height="16" fill="var(--bar-dark)"/>
          <rect x="18" y="-28" width="5" height="28" fill="var(--bar-light)"/><rect x="18" y="-17" width="5" height="17" fill="var(--bar-dark)"/>
          <rect x="27" y="-48" width="5" height="48" fill="var(--bar-light)"/><rect x="27" y="-24" width="5" height="24" fill="var(--bar-dark)"/>
          <rect x="36" y="-44" width="5" height="44" fill="var(--bar-light)"/><rect x="36" y="-24" width="5" height="24" fill="var(--bar-dark)"/>
          <rect x="45" y="-40" width="5" height="40" fill="var(--bar-light)"/><rect x="45" y="-22" width="5" height="22" fill="var(--bar-dark)"/>
          <rect x="54" y="-30" width="5" height="30" fill="var(--bar-light)"/><rect x="54" y="-20" width="5" height="20" fill="var(--bar-dark)"/>
          <rect x="63" y="-26" width="5" height="26" fill="var(--bar-light)"/><rect x="63" y="-18" width="5" height="18" fill="var(--bar-dark)"/>
          <rect x="72" y="-34" width="5" height="34" fill="var(--bar-light)"/><rect x="72" y="-20" width="5" height="20" fill="var(--bar-dark)"/>
          <rect x="81" y="-24" width="5" height="24" fill="var(--bar-light)"/><rect x="81" y="-16" width="5" height="16" fill="var(--bar-dark)"/>
          <rect x="90" y="-30" width="5" height="30" fill="var(--bar-light)"/><rect x="90" y="-18" width="5" height="18" fill="var(--bar-dark)"/>
          <rect x="99" y="-32" width="5" height="32" fill="var(--bar-light)"/><rect x="99" y="-18" width="5" height="18" fill="var(--bar-dark)"/>
          <line x1="-3" y1="0" x2="107" y2="0" stroke="#cfcfcf" stroke-width=".5"/>
        </g>
        <g id="axis-labels">
          <text class="s-tiny" x="0" y="5">Text Text Text Text Text Text Text Text Text Text Text Text</text>
        </g>
      </defs>
      <text class="s-title" x="192" y="20" text-anchor="middle">Lorem ipsum dolor sit amet</text>
      <text class="s-sub" x="192" y="33" text-anchor="middle">Lorem ipsum dolor sit amet, consectetuer adipiscing elit. Aenean commodo ligula eget dolor.</text>

      <text class="s-head" x="27" y="55">Lorem ipsum</text>
      <text class="s-tiny" x="27" y="60">Lorem ipsum dolor sit amet, consectetuer sadipscing elitr</text>
      <use href="#bars-a" x="30" y="117"/><use href="#axis-labels" x="28" y="117"/>

      <text class="s-head" x="150" y="55">Lorem ipsum</text>
      <text class="s-tiny" x="150" y="60">Lorem ipsum dolor sit amet, consectetuer sadipscing elitr</text>
      <use href="#bars-b" x="148" y="117"/><use href="#axis-labels" x="146" y="117"/>

      <text class="s-head" x="27" y="134">Lorem ipsum</text>
      <text class="s-tiny" x="27" y="139">Lorem ipsum dolor sit amet, consectetuer sadipscing elitr</text>
      <use href="#bars-b" x="30" y="196"/><use href="#axis-labels" x="28" y="196"/>

      <text class="s-head" x="150" y="134">Lorem ipsum</text>
      <text class="s-tiny" x="150" y="139">Lorem ipsum dolor sit amet, consectetuer sadipscing elitr</text>
      <use href="#bars-a" x="148" y="196"/><use href="#axis-labels" x="146" y="196"/>
      <rect x="262" y="183" width="3" height="3" fill="var(--bar-light)"/><text class="s-tiny" x="267" y="186">Lorem</text>
      <rect x="262" y="190" width="3" height="3" fill="var(--bar-dark)"/><text class="s-tiny" x="267" y="193">Ipsum</text>

      <g class="s-tiny">
        <text x="286" y="76">• Lorem ipsum dolor sit amet,</text>
        <text x="290" y="81">consetetur sadipscing elitr, sed</text>
        <text x="290" y="86">diam nonumy eirmod tempor</text>
        <text x="290" y="91">invidunt ut labore et dolore</text>
        <text x="290" y="96">magna aliquyam erat, sed diam.</text>
        <text x="286" y="120">• Lorem ipsum dolor sit amet,</text>
        <text x="290" y="125">consetetur sadipscing elitr, sed</text>
        <text x="290" y="130">diam nonumy eirmod tempor</text>
        <text x="290" y="135">invidunt ut labore et dolore</text>
        <text x="290" y="140">magna aliquyam erat, sed diam.</text>
        <text x="286" y="164">• Lorem ipsum dolor sit amet,</text>
        <text x="290" y="169">consetetur sadipscing elitr, sed</text>
        <text x="290" y="174">diam nonumy eirmod tempor</text>
        <text x="290" y="179">invidunt ut labore et dolore</text>
        <text x="290" y="184">magna aliquyam erat, sed diam.</text>
      </g>
      <text class="s-tiny" x="368" y="211">31</text>
    </svg>
  </div>

  <!-- Slide: bar and line combo chart -->
  <div class="slide slide--combo">
    <svg viewBox="0 0 385 217">
      <text class="s-title" x="192" y="20" text-anchor="middle">Lorem ipsum dolor sit amet</text>
      <text class="s-sub" x="192" y="33" text-anchor="middle">Lorem ipsum dolor sit amet, consectetuer adipiscing elit. Aenean commodo ligula eget dolor.</text>

      <g class="s-tiny" style="font-size:4.6px">
        <text x="26" y="91">• Lorem ipsum dolor sit amet,</text>
        <text x="30" y="97">consetetur sadipscing elitr,</text>
        <text x="30" y="103">sed diam nonumy eirmod</text>
        <text x="30" y="109">tempor invidunt ut labore et</text>
        <text x="30" y="115">dolore magna aliquyam erat,</text>
        <text x="30" y="121">sed diam voluptua. At vero</text>
        <text x="30" y="127">eos et accusam.</text>
        <text x="26" y="148">• Lorem ipsum dolor sit amet,</text>
        <text x="30" y="154">consetetur sadipscing elitr,</text>
        <text x="30" y="160">sed diam nonumy eirmod</text>
        <text x="30" y="166">tempor invidunt ut labore et</text>
        <text x="30" y="172">dolore magna aliquyam erat,</text>
        <text x="30" y="178">sed diam voluptua. At vero</text>
        <text x="30" y="184">eos et accusam.</text>
      </g>

      <g fill="var(--bar-light)">
        <rect x="116" y="149" width="11" height="41"/>
        <rect x="133.5" y="146" width="11" height="44"/>
        <rect x="151" y="136.4" width="11" height="53.6"/>
        <rect x="168.5" y="123.8" width="11" height="66.2"/>
        <rect x="186" y="120.7" width="11" height="69.3"/>
        <rect x="203.5" y="114.4" width="11" height="75.6"/>
        <rect x="221" y="114.4" width="11" height="75.6"/>
        <rect x="238.5" y="98.6" width="11" height="91.4"/>
        <rect x="256" y="98.6" width="11" height="91.4"/>
        <rect x="273.5" y="92.3" width="11" height="97.7"/>
        <rect x="291" y="89.2" width="11" height="100.8"/>
        <rect x="308.5" y="82.9" width="11" height="107.1"/>
      </g>
      <g class="s-value" text-anchor="middle">
        <text x="121.5" y="173">13</text><text x="139" y="173">14</text><text x="156.5" y="167">17</text>
        <text x="174" y="160">21</text><text x="191.5" y="158">22</text><text x="209" y="155">24</text>
        <text x="226.5" y="155">24</text><text x="244" y="147">29</text><text x="261.5" y="147">29</text>
        <text x="279" y="144">31</text><text x="296.5" y="142">32</text><text x="314" y="140">34</text>
      </g>
      <polyline fill="none" stroke="#9a9a9a" stroke-width=".7"
        points="121.5,139.6 139,136.4 156.5,127 174,114.4 191.5,111.3 209,105 226.5,98.7 244,89.2 261.5,89.2 279,82.9 296.5,76.6 314,76.6"/>
      <g fill="var(--white)" stroke="#9a9a9a" stroke-width=".6">
        <circle cx="121.5" cy="139.6" r="1.4"/><circle cx="139" cy="136.4" r="1.4"/><circle cx="156.5" cy="127" r="1.4"/>
        <circle cx="174" cy="114.4" r="1.4"/><circle cx="191.5" cy="111.3" r="1.4"/><circle cx="209" cy="105" r="1.4"/>
        <circle cx="226.5" cy="98.7" r="1.4"/><circle cx="244" cy="89.2" r="1.4"/><circle cx="261.5" cy="89.2" r="1.4"/>
        <circle cx="279" cy="82.9" r="1.4"/><circle cx="296.5" cy="76.6" r="1.4"/><circle cx="314" cy="76.6" r="1.4"/>
      </g>
      <g class="s-label" text-anchor="middle">
        <text x="121.5" y="135">16</text><text x="139" y="132">17</text><text x="156.5" y="123">20</text>
        <text x="174" y="110">24</text><text x="191.5" y="107">25</text><text x="209" y="101">27</text>
        <text x="226.5" y="94">29</text><text x="244" y="85">32</text><text x="261.5" y="85">32</text>
        <text x="279" y="78">34</text><text x="296.5" y="72">36</text><text x="314" y="72">36</text>
      </g>
      <g class="s-label" text-anchor="middle">
        <text x="121.5" y="199">Text</text><text x="139" y="199">Text</text><text x="156.5" y="199">Text</text>
        <text x="174" y="199">Text</text><text x="191.5" y="199">Text</text><text x="209" y="199">Text</text>
        <text x="226.5" y="199">Text</text><text x="244" y="199">Text</text><text x="261.5" y="199">Text</text>
        <text x="279" y="199">Text</text><text x="296.5" y="199">Text</text><text x="314" y="199">Text</text>
      </g>
      <text class="s-label" x="324" y="79">Lorem ipsum</text>
      <text class="s-accent" x="325" y="140">Lorem ipsum</text>
      <text class="s-tiny" x="361" y="211">34</text>
    </svg>
  </div>

  <!-- Slide: horizontal ranking with change column -->
  <div class="slide slide--ranking">
    <svg viewBox="0 0 385 217">
      <text class="s-title" x="192" y="20" text-anchor="middle">Lorem ipsum dolor sit amet</text>
      <text class="s-sub" x="192" y="33" text-anchor="middle">Lorem ipsum dolor sit amet, consectetuer adipiscing elit. Aenean commodo ligula eget dolor.</text>
      <text class="s-head" x="39" y="50">Lorem ipsum</text>
      <text class="s-tiny" x="39" y="56" style="font-size:4px">Lorem ipsum dolor sit amet, consetetur sadipscing elitr, sed diam nonumy eirmod tempor</text>
      <text class="s-tiny" x="39" y="61" style="font-size:4px">invidunt ut labore et dolore magna aliquyam erat, sed diam voluptua. At vero eos et accusam.</text>

      <g class="s-label">
        <text x="25" y="77">Text</text><text x="25" y="88.8">Text</text><text x="25" y="100.6">Text</text>
        <text x="25" y="112.4">Text</text><text x="25" y="124.2">Text</text><text x="25" y="136">Text</text>
        <text x="25" y="147.8">Text</text><text x="25" y="159.6">Text</text><text x="25" y="171.4">Text</text>
        <text x="25" y="183.2">Text</text>
      </g>
      <g fill="var(--bar-dark)">
        <rect x="41" y="73" width="105" height="5"/>
        <rect x="41" y="84.8" width="88" height="5"/>
        <rect x="41" y="96.6" width="78" height="5"/>
        <rect x="41" y="108.4" width="78" height="5"/>
        <rect x="41" y="120.2" width="82" height="5"/>
        <rect x="41" y="132" width="75" height="5"/>
        <rect x="41" y="143.8" width="71" height="5"/>
        <rect x="41" y="155.6" width="58" height="5"/>
        <rect x="41" y="167.4" width="48" height="5"/>
        <rect x="41" y="179.2" width="44" height="5"/>
      </g>
      <g class="s-label">
        <text x="149" y="77.5">31</text><text x="132" y="89.3">26</text><text x="122" y="101.1">23</text>
        <text x="122" y="112.9">23</text><text x="126" y="124.7">24</text><text x="119" y="136.5">22</text>
        <text x="115" y="148.3">21</text><text x="102" y="160.1">17</text><text x="92" y="171.9">14</text>
        <text x="88" y="183.7">13</text>
      </g>
      <g stroke="#dedede" stroke-width=".4">
        <line x1="40" y1="81" x2="180" y2="81"/><line x1="40" y1="92.8" x2="180" y2="92.8"/>
        <line x1="40" y1="104.6" x2="180" y2="104.6"/><line x1="40" y1="116.4" x2="180" y2="116.4"/>
        <line x1="40" y1="128.2" x2="180" y2="128.2"/><line x1="40" y1="140" x2="180" y2="140"/>
        <line x1="40" y1="151.8" x2="180" y2="151.8"/><line x1="40" y1="163.6" x2="180" y2="163.6"/>
        <line x1="40" y1="175.4" x2="180" y2="175.4"/>
        <line x1="190" y1="81" x2="270" y2="81"/><line x1="190" y1="92.8" x2="270" y2="92.8"/>
        <line x1="190" y1="104.6" x2="270" y2="104.6"/><line x1="190" y1="116.4" x2="270" y2="116.4"/>
        <line x1="190" y1="128.2" x2="270" y2="128.2"/><line x1="190" y1="140" x2="270" y2="140"/>
        <line x1="190" y1="151.8" x2="270" y2="151.8"/><line x1="190" y1="163.6" x2="270" y2="163.6"/>
        <line x1="190" y1="175.4" x2="270" y2="175.4"/>
      </g>
      <g fill="var(--bar-light)">
        <rect x="222" y="73" width="24" height="5"/>
        <rect x="222" y="84.8" width="30" height="5"/>
        <rect x="210" y="96.6" width="12" height="5"/>
        <rect x="216" y="108.4" width="6" height="5"/>
        <rect x="222" y="120.2" width="24" height="5"/>
        <rect x="222" y="132" width="16" height="5"/>
        <rect x="222" y="143.8" width="8" height="5"/>
        <rect x="216" y="155.6" width="6" height="5"/>
        <rect x="222" y="167.4" width="30" height="5"/>
        <rect x="222" y="179.2" width="16" height="5"/>
      </g>
      <g class="s-accent">
        <text x="249" y="77.5">+3%</text><text x="255" y="89.3">+4%</text>
        <text x="195" y="101.1">-2%</text><text x="204" y="112.9">-1%</text>
        <text x="249" y="124.7">+3%</text><text x="241" y="136.5">+2%</text>
        <text x="233" y="148.3">+1%</text><text x="204" y="160.1">-1%</text>
        <text x="255" y="171.9">+4%</text><text x="241" y="183.7">+2%</text>
      </g>
      <g class="s-tiny">
        <text x="282" y="75">• Lorem ipsum dolor sit amet,</text>
        <text x="286" y="80">consetetur sadipscing elitr, sed</text>
        <text x="286" y="85">diam nonumy eirmod tempor</text>
        <text x="286" y="90">invidunt ut labore et dolore</text>
        <text x="286" y="95">magna aliquyam erat, sed diam.</text>
        <text x="282" y="119">• Lorem ipsum dolor sit amet,</text>
        <text x="286" y="124">consetetur sadipscing elitr, sed</text>
        <text x="286" y="129">diam nonumy eirmod tempor</text>
        <text x="286" y="134">invidunt ut labore et dolore</text>
        <text x="286" y="139">magna aliquyam erat, sed diam.</text>
        <text x="282" y="163">• Lorem ipsum dolor sit amet,</text>
        <text x="286" y="168">consetetur sadipscing elitr, sed</text>
        <text x="286" y="173">diam nonumy eirmod tempor</text>
        <text x="286" y="178">invidunt ut labore et dolore</text>
        <text x="286" y="183">magna aliquyam erat, sed diam.</text>
      </g>
      <text class="s-tiny" x="361" y="211">36</text>
    </svg>
  </div>

  <div class="title-band">
    <h1>Standard Graphs</h1>
    <p>SlideCraft Presentation 1</p>
  </div>
</div>
</body>
</html>
```